Website Quibrel Outdoor

Hi I'm looking for a simple design for a new website. It's outdoor products mainly in category, Boat, Tarpaulin, Fishing, Golf. I have include image and text for 8 products + presentation etc. I want a simple and modern site + fast + Mobile. Wordpress. I'm going to sell through Tradovik so I don't need any WooCommerce but a buy button to Tradovik. I haven set up the Tradovik account yet. My logo i s grey and orange. My goal is to sell in Tradovik US and later EU.

```html
<!DOCTYPE html>
<html lang="en">
<head>
<meta charset="utf-8">
<title>Quibrel Outdoor</title>
<link href="https://fonts.googleapis.com/css2?family=Poppins:wght@500;600;700&family=Roboto:wght@400;500&display=swap" rel="stylesheet">
<style>
:root{
  --orange:#f07d14;
  --ink:#2b2b2b;
  --grey:#555;
  --light:#fff;
}
*{box-sizing:border-box;margin:0;padding:0}
html,body{width:1200px;height:3361px;overflow:hidden;background:#fff}
body{position:relative;font-family:'Roboto',sans-serif;color:var(--ink)}
.abs{position:absolute}
.btn{position:absolute;display:flex;align-items:center;justify-content:center;width:170px;height:54px;background:var(--orange);color:#fff;font:500 16px 'Roboto',sans-serif;border-radius:4px;text-decoration:none}
.brand{font-family:'Poppins',sans-serif;font-weight:600;color:var(--orange);text-align:center;line-height:1.05;letter-spacing:1px}

/* header */
.topstrip{left:0;top:0;width:1200px;height:52px;background:linear-gradient(90deg,#4a4d4e,#6a6e70,#56595a)}
.navbar{left:0;top:52px;width:1200px;height:55px;background:#fff;border-bottom:1px solid #eee}
.nav a{position:absolute;top:70px;font-size:15px;color:#555;text-decoration:none}
.logo-disc{left:541px;top:19px;width:118px;height:118px;border-radius:50%;background:#fff;display:flex;align-items:center;justify-content:center}
.logo-disc .brand{font-size:17px}
.search-text{left:852px;top:69px;font-size:13px;color:#888;width:87px;border-bottom:1px solid #999;padding-bottom:3px}
.badge{left:983px;top:55px;width:18px;height:18px;border-radius:50%;background:var(--orange);color:#fff;font-size:11px;display:flex;align-items:center;justify-content:center}

/* hero */
.hero{left:0;top:107px;width:1200px;height:578px;background:linear-gradient(180deg,#5a6356 0%,#3f4a3a 35%,#4b4f4c 65%,#2e3330 100%)}
.hero-frame{left:261px;top:315px;width:712px;height:147px;border:2px solid #fff;border-top:none}
.hero-frame-top{top:315px;height:2px;background:#fff}
.hero-title{left:261px;top:290px;width:712px;text-align:center;font:700 42px/53px 'Poppins',sans-serif;color:#fff}

/* categories */
.cat{position:absolute;top:769px;width:279px;height:307px;display:flex;align-items:center;justify-content:center;color:#fff;font:500 33px 'Poppins',sans-serif}
.cat-frame{position:absolute;left:7px;top:7px;right:7px;bottom:7px;border:2px solid #fff}
.cat-list{position:absolute;left:62px;top:118px;font:400 17px/33px 'Roboto',sans-serif}
.cat-title{position:absolute;left:0;right:0;top:38px;text-align:center}

/* about */
.about-band{left:0;top:1262px;width:1200px;height:685px;background:linear-gradient(135deg,#1b2740 0%,#22355e 35%,#2a2a30 70%,#3b2a1f 100%)}
.about-card{left:300px;top:1347px;width:600px;height:467px;background:#fff}
.sec-title{font:500 31px 'Poppins',sans-serif;color:var(--grey);text-align:center}
.sec-title b{color:var(--orange);font-weight:500}
.rule{height:2px;background:var(--orange)}
.about-text{left:355px;top:1480px;width:490px;text-align:center;font-size:17px;line-height:30px;color:#444}

/* products */
.prod{position:absolute;top:2171px;width:220px;text-align:center}
.prod .img{width:190px;height:200px;margin:0 auto;border-radius:6px}
.prod .name{margin-top:30px;font-size:17px;line-height:26px;color:#333;text-transform:uppercase}
.prod .stars{margin-top:6px;display:flex;justify-content:center}
.prod .price{margin-top:8px;font-size:17px;color:#222}

/* discount */
.promo{left:0;top:2637px;width:1200px;height:287px;background:linear-gradient(90deg,#6c6a3e 0%,#8a8145 45%,#9a8a4a 70%,#5f6840 100%)}
.promo-title{left:112px;top:2718px;font:700 40px/50px 'Poppins',sans-serif;color:#fff}

/* footer */
.foot-nav a{position:absolute;top:3124px;font-size:17px;color:#222;text-decoration:none}
.tradovik{left:556px;top:3166px;width:88px;height:34px;border-radius:4px;box-shadow:0 1px 4px rgba(0,0,0,.25);display:flex;align-items:center;justify-content:center;font:500 15px 'Roboto',sans-serif;color:#222}
.foot-text{left:200px;width:800px;text-align:center;font-size:15px;line-height:30px;color:#222}
</style>
</head>
<body>

<!-- Header -->
<div class="abs topstrip" role="img" aria-label="Mountain landscape photo continuing behind the header"></div>
<div class="abs navbar"></div>
<nav class="nav">
  <a style="left:110px">Home</a>
  <a style="left:177px">Shop</a>
  <a style="left:240px">Featured</a>
  <a style="left:329px">Pages</a>
  <a style="left:399px">Blogs</a>
</nav>
<div class="abs logo-disc"><div class="brand">QUIBREL<br>OUTDOOR</div></div>
<svg class="abs" style="left:818px;top:66px" width="24" height="24" viewBox="0 0 24 24" fill="none" stroke="#555" stroke-width="2"><circle cx="10" cy="10" r="7"/><path d="M15 15l6 6"/></svg>
<div class="abs search-text">Search</div>
<svg class="abs" style="left:964px;top:66px" width="22" height="24" viewBox="0 0 22 24" fill="none" stroke="#555" stroke-width="2"><path d="M3 7h16l-1 15H4z"/><path d="M7 9V5a4 4 0 018 0v4"/></svg>
<div class="abs badge">0</div>
<svg class="abs" style="left:1017px;top:67px" width="26" height="22" viewBox="0 0 26 22" fill="none" stroke="#555" stroke-width="2"><path d="M13 20S2 13 2 7a5.5 5.5 0 0111-1 5.5 5.5 0 0111 1c0 6-11 13-11 13z"/></svg>
<svg class="abs" style="left:1064px;top:66px" width="24" height="24" viewBox="0 0 24 24" fill="none" stroke="#555" stroke-width="2"><circle cx="12" cy="12" r="10"/><circle cx="12" cy="10" r="3.5"/><path d="M5.5 19a8 8 0 0113 0"/></svg>

<!-- Hero -->
<div class="abs hero" role="img" aria-label="Hikers climbing a rocky mountain trail beside a stream"></div>
<div class="abs hero-frame"></div>
<div class="abs hero-frame-top" style="left:261px;width:44px"></div>
<div class="abs hero-frame-top" style="left:895px;width:78px"></div>
<h1 class="abs hero-title">BEST OUTDOOR EXPERIENCE<br>WITH QUIBREL OUTDOOR</h1>
<a class="btn" style="left:515px;top:434px">Get Started</a>

<!-- Categories -->
<div class="cat" style="left:17px;background:linear-gradient(180deg,#8a8f96,#4c5560 60%,#39424c)" role="img" aria-label="Motor boat on the water at dusk"><span style="margin-top:60px">BÅT</span></div>
<div class="cat" style="left:313px;background:linear-gradient(180deg,#2f5f8f 0%,#b9a889 45%,#5d7d3a 80%)" role="img" aria-label="Tarpaulin shelter pitched on a grass field"><span style="margin-top:60px">PRESENNING</span></div>
<div class="cat" style="left:608px;background:#3b4a2c" role="img" aria-label="Golf bag with clubs, darkened">
  <div class="cat-frame"></div>
  <div class="cat-title">OUTDOOR</div>
  <div class="cat-list">» Fenderskydd brygga<br>» Golfhandduk<br>» Glasogon flugfiske<br>» Kylvaska camping<br>&nbsp;&nbsp;&nbsp;bord</div>
</div>
<div class="cat" style="left:904px;background:linear-gradient(180deg,#b8c0c3,#c0642c 55%,#3a3f3c)" role="img" aria-label="Angler in an orange jacket holding a fly fishing rod"><span style="margin-top:60px">INDOOR</span></div>
<a class="btn" style="left:515px;top:1121px">Get Started</a>

<!-- About -->
<div class="abs about-band" role="img" aria-label="Night camping scene with pine forest, campfire and glowing orange tent"></div>
<div class="abs about-card"></div>
<h2 class="abs sec-title" style="left:300px;top:1390px;width:600px"><b>About</b> Us</h2>
<div class="abs rule" style="left:558px;top:1441px;width:85px"></div>
<p class="abs about-text">Nemo enim ipsam voluptatem quia voluptas sit aspernatur aut odit aut fugit, sed quia consequuntur magni dolores eos qui ratione voluptatem sequi nesciunt. Neque porro quisquam est, qui dolorem ipsum quia dolor sit amet, consectetur, adipisci velit, sed quia non numquam eius modi tempora incidunt ut labore et dolore magnam aliquam quaerat voluptatem. Ut enim ad minima veniam, quis nostrum exe laboriosam.</p>
<a class="btn" style="left:515px;top:1722px">Read More</a>

<!-- Featured products -->
<h2 class="abs sec-title" style="left:300px;top:2030px;width:600px"><b>Featured</b> Products</h2>
<div class="abs rule" style="left:515px;top:2083px;width:170px"></div>

<svg width="0" height="0" style="position:absolute"><defs><path id="star" d="M8 0l2.4 5 5.6.6-4.2 3.8 1.2 5.6L8 12.2 3 15l1.2-5.6L0 5.6 5.6 5z"/></defs></svg>

<div class="prod" style="left:120px">
  <div class="img" style="background:linear-gradient(160deg,#f2f2f2,#c9c9c9)" role="img" aria-label="Clear water bag tarpaulin weight"></div>
  <div class="name">Presenningsvikt -<br>dunk</div>
  <div class="stars"><svg width="100" height="16" viewBox="0 0 100 16"><g fill="#f07d14"><use href="#star"/><use href="#star" x="21"/><use href="#star" x="42"/><use href="#star" x="63"/><use href="#star" x="84"/></g></svg></div>
  <div class="price">$59.00</div>
</div>
<div class="prod" style="left:366px">
  <div class="img" style="background:linear-gradient(160deg,#f4f4f4,#d6d6d6 50%,#f4f4f4)" role="img" aria-label="Grey golf towel with orange edge on a clip holder"></div>
  <div class="name">Hållare med<br>löstagbar handduk<br>för golf</div>
  <div class="stars"><svg width="100" height="16" viewBox="0 0 100 16"><g fill="#f07d14"><use href="#star"/><use href="#star" x="21"/><use href="#star" x="42"/><use href="#star" x="63"/><use href="#star" x="84"/></g></svg></div>
  <div class="price">$59.00</div>
</div>
<div class="prod" style="left:612px">
  <div class="img" style="background:linear-gradient(160deg,#f6f6f6,#dcdcdc 50%,#f6f6f6)" role="img" aria-label="White sunglasses with black lanyard"></div>
  <div class="name">Läsglasögon -<br>sytillbehör</div>
  <div class="stars"><svg width="100" height="16" viewBox="0 0 100 16"><g fill="#f07d14"><use href="#star"/><use href="#star" x="21"/><use href="#star" x="42"/><use href="#star" x="63"/><use href="#star" x="84"/></g></svg></div>
  <div class="price">$59.00</div>
</div>
<div class="prod" style="left:859px">
  <div class="img" style="background:linear-gradient(160deg,#2e9a4f,#e9efe9 55%,#2c6fb0)" role="img" aria-label="Sheets of green and blue boat safety sticker labels"></div>
  <div class="name">Översiktsplan &amp;<br>klisteretiketter</div>
  <div class="stars"><svg width="100" height="16" viewBox="0 0 100 16"><g fill="#f07d14"><use href="#star"/><use href="#star" x="21"/><use href="#star" x="42"/><use href="#star" x="63"/><use href="#star" x="84"/></g></svg></div>
  <div class="price">$59.00</div>
</div>

<!-- Discount -->
<div class="abs promo" role="img" aria-label="Two people fishing from a small boat on a calm lake at sunset"></div>
<h2 class="abs promo-title">SPECIAL DISCOUNT<br>UPTO 50% OFF</h2>
<a class="btn" style="left:111px;top:2821px">View All</a>

<!-- Footer -->
<div class="abs brand" style="left:450px;top:3040px;width:300px;font-size:30px;line-height:36px">QUIBREL<br>OUTDOOR</div>
<nav class="foot-nav">
  <a style="left:399px">HOME</a>
  <a style="left:477px">SHOP</a>
  <a style="left:553px">FEATURED</a>
  <a style="left:664px">PAGES</a>
  <a style="left:746px">BLOGS</a>
</nav>
<div class="abs tradovik">Tradovik</div>
<p class="abs foot-text" style="top:3218px">Nemo enim ipsam voluptatem quia voluptas sit aspernatur aut odit aut fugit, sed quia consequuntur magni dolores<br>eos qui ratione voluptatem sequi nesciunt.</p>
<p class="abs foot-text" style="top:3286px">2021 QUIBREL OUTDOOR. ALL RIGHTS RESERVED.</p>

</body>
</html>
```